Business Card Design Project

I have established a company called "Corvella" which is a business specialising in psychotherapy/counselling , predominantly for anxiety & depression.

My name is Nel....hence, the Corvella link. However, Corvella was also chosen for its reference to green shoots of growth/recovery.

Corvella is to be "upmarket" and highly professional. I'm keen for the style and colours to reflect this.....taupe/grey with navy/black script, for example.....NO primary colours.

My name needs to be on the card and my mobile number. Not sure, but suspect it should also have my qualifications ( BA (Psych) & BSc (Hons) Psychology). Mobile number 0412 903 618.

```html
<!DOCTYPE html>
<html lang="en">
<head>
<meta charset="utf-8">
<title>Corvella – Business Card Front</title>
<link rel="stylesheet" href="https://fonts.googleapis.com/css2?family=Source+Sans+3:wght@300;400;600&display=swap">
<style>
  :root {
    --page-bg: #ececea;
    --card-dark: #5f6061;
    --card-mid: #7c7d7e;
    --card-light: #9a9b9c;
    --band-light: #c4c5c6;
    --photo-light: #e0e0df;
    --photo-mid: #bdbdbc;
    --photo-dark: #a9a9a8;
    --name-navy: #3d3fae;
    --brand-green: #8cbc3c;
    --ink: #0e0e0e;
    --tagline: #ffffff;
  }

  * { margin: 0; padding: 0; box-sizing: border-box; }

  html, body {
    width: 1026px;
    height: 1200px;
    overflow: hidden;
    background: var(--page-bg);
    font-family: "Source Sans 3", "Myriad Pro", Arial, sans-serif;
  }

  .canvas {
    position: relative;
    width: 1026px;
    height: 1200px;
  }

  .business-card {
    position: absolute;
    left: 63px;
    top: 351px;
    width: 900px;
    height: 497px;
    overflow: hidden;
    background: linear-gradient(100deg, var(--card-dark) 0%, var(--card-mid) 55%, var(--card-light) 100%);
  }

  .portrait-area {
    position: absolute;
    left: 0;
    top: 0;
    width: 285px;
    height: 100%;
    background: linear-gradient(90deg, var(--photo-light) 0%, var(--photo-mid) 55%, var(--photo-dark) 100%);
  }

  .divider-band {
    position: absolute;
    left: 285px;
    top: 0;
    width: 63px;
    height: 100%;
    background: linear-gradient(90deg, var(--band-light) 0%, var(--card-light) 100%);
  }

  .identity {
    position: absolute;
    right: 52px;
    top: 70px;
    text-align: right;
  }

  .person-name {
    font-weight: 300;
    font-size: 96px;
    line-height: 0.8;
    letter-spacing: 1px;
    color: var(--name-navy);
  }

  .brand-name {
    margin-top: 6px;
    margin-right: -4px;
    font-weight: 400;
    font-size: 60px;
    line-height: 0.95;
    color: var(--brand-green);
  }

  .credentials {
    position: absolute;
    right: 73px;
    top: 228px;
    text-align: right;
    color: var(--ink);
    font-size: 30px;
    line-height: 38px;
    font-weight: 400;
  }

  .mobile { margin-top: 10px; }

  .tagline {
    position: absolute;
    left: 285px;
    top: 412px;
    font-size: 39px;
    font-weight: 400;
    color: var(--tagline);
    white-space: nowrap;
  }
</style>
</head>
<body>
  <main class="canvas">
    <section class="business-card" aria-label="Corvella business card, front">
      <div class="portrait-area" role="img" aria-label="Soft-focus photograph of a standing figure"></div>
      <div class="divider-band" role="img" aria-label="Fine diagonal line texture"></div>

      <div class="identity">
        <p class="person-name">NEL</p>
        <p class="brand-name">Corvella</p>
      </div>

      <div class="credentials">
        <p>BA (Psych)</p>
        <p>BSc (Hons) Psychology</p>
        <p class="mobile">Mobile: 0412 903 618</p>
      </div>

      <p class="tagline">Specialising In Psychotherapy</p>
    </section>
  </main>
</body>
</html>
```